Heron Loan Partners Business Card

We need a business card design for our mortgage servicing company. In addition to servicing the loans of homeowners, we help homeowners with purchasing their homes and any mortgage refinancing. We would like to see designs that use the colors in the logo attached below (gold-ish yellow and navy blue), and any other design you deem fit! The design should communicate a simpler life with smart mortgages provided by Heron.

```html
<!DOCTYPE html>
<html lang="en">
<head>
<meta charset="utf-8">
<title>Heron Loan Partners Business Card</title>
<link rel="stylesheet" href="https://fonts.googleapis.com/css2?family=Open+Sans:wght@400;600;700&display=swap">
<style>
  :root {
    --stage: #222222;
    --paper: #ffffff;
    --gold: #e0ab35;
    --navy: #201a4f;
    --ink: #111111;
  }
  * { margin: 0; padding: 0; box-sizing: border-box; }
  html, body {
    width: 1200px; height: 780px; overflow: hidden;
    background: var(--stage);
    font-family: "Open Sans", Arial, sans-serif;
  }
  .stage {
    width: 1200px; height: 780px;
    display: flex; align-items: center; justify-content: center; gap: 40px;
  }
  .card {
    position: relative;
    width: 540px; height: 309px;
    background: var(--paper);
    border-bottom: 5px solid var(--gold);
    box-shadow: 0 10px 24px rgba(0,0,0,0.55);
  }
  .brand {
    display: flex; align-items: center; gap: 10px;
    font-weight: 700; color: var(--navy);
    white-space: nowrap;
  }
  .brand-dot {
    width: 14px; height: 14px; border-radius: 50%;
    background: var(--gold); flex: none;
  }
  .card-front .brand {
    position: absolute; left: 50%; top: 50%;
    transform: translate(-50%, -50%);
    font-size: 36px;
  }
  .card-front .brand-dot { width: 22px; height: 22px; }
  .card-back .brand {
    position: absolute; left: 34px; top: 34px;
    font-size: 22px;
  }
  .contact {
    position: absolute; left: 34px; right: 30px; bottom: 30px;
    color: var(--ink);
  }
  .person { font-size: 26px; font-weight: 700; line-height: 1.1; margin-bottom: 12px; }
  .person .first { color: var(--gold); }
  .person .last { color: var(--ink); }
  .person .role { color: var(--gold); font-size: 15px; font-weight: 400; margin-left: 6px; }
  .details {
    display: flex; justify-content: space-between;
    font-size: 12.5px; margin-bottom: 6px;
  }
  .details .label { color: var(--gold); font-weight: 600; margin-right: 3px; }
  .address { font-size: 12.5px; }
</style>
</head>
<body>
  <main class="stage">
    <section class="card card-front" aria-label="Business card front">
      <div class="brand"><span class="brand-dot"></span>Heron Loan Partners</div>
    </section>

    <section class="card card-back" aria-label="Business card back">
      <div class="brand"><span class="brand-dot"></span>Heron Loan Partners</div>
      <div class="contact">
        <p class="person"><span class="first">Lena</span> <span class="last">Varga</span><span class="role">CEO</span></p>
        <p class="details">
          <span><span class="label">T:</span>(555) 214-3087</span>
          <span><span class="label">E:</span>info@example.com</span>
          <span><span class="label">W:</span>www.example.com</span>
        </p>
        <p class="address">418 Elmcrest Ave. Suite 300 Lakeview, TX 75001</p>
      </div>
    </section>
  </main>
</body>
</html>
```